Construction Company looking to change the way General Contractors are perceived today

Looking for a 10-12 page professional web design that includes social media integration, contact form, multiple ways to contact us, services provided, about page, testimonials, project portfolio, downloadable resources, mobile friendly, media gallery, blog, Subcontractors/Bids tab
Must have editing abilities.
I like parallax scrolling, autoplay,
Here is a great example of a site I like. https://marlowstoneworks.com/

Target Market(s)

Commercial and Industrial Owners and Project Managers, Residential Home and Multifamily Owners, Architects and Engineers

Industry/Entity Type

Construction, Pre-construction, Construction Management

Coding

Number of Pages Required

5+ page

Colors

Designer to choose colors to be used in the design.

Requirements
Must have
• TRI-BAY GROUP (Business name) services General Contracting, Construction Management, Pre-construction Services, Home Renovations, Additions, Exterior Spaces, Commercial Construction, Interior buildouts, Office Space Renovations.
Nice to have
• Full-Service General Contractor, Family Oriented - Client Focused, Owner Involved, Relationship Focused, Superior Workmanship, Communication Driven

```html
<!DOCTYPE html>
<html lang="en">
<head>
<meta charset="utf-8">
<title>Tri-Bay Group — General Contractors</title>
<link rel="stylesheet" href="https://fonts.googleapis.com/css2?family=Bebas+Neue&family=Orbitron:wght@700&family=Arimo:wght@400;700&display=swap">
<style>
:root{
  --blue:#1a82e8;
  --blue-deep:#0e6bd0;
  --blue-pale:#cfe4fb;
  --ink:#333333;
  --muted:#666666;
  --white:#ffffff;
  --line:#9aa3ad;
  --gold:#f5b800;
  --shadow:0 4px 14px rgba(0,0,0,.18);
}
*{box-sizing:border-box;margin:0;padding:0}
html,body{width:1200px;height:5172px;overflow:hidden;background:var(--white)}
body{position:relative;font-family:"Arimo",Arial,sans-serif;color:var(--ink)}
.abs{position:absolute}
.heading{font-family:"Bebas Neue",Impact,sans-serif;letter-spacing:.5px;font-weight:400}
.section-title{position:absolute;left:0;width:1200px;text-align:center;font-family:"Bebas Neue",Impact,sans-serif;font-size:34px;color:var(--blue)}
.section-title.on-blue{color:var(--white)}
.photo{position:absolute;overflow:hidden}
.btn{position:absolute;display:flex;align-items:center;justify-content:center;font-family:"Bebas Neue",Impact,sans-serif;font-size:19px;color:var(--blue);background:var(--white);border:1px solid #c9d6e4;box-shadow:0 2px 6px rgba(0,0,0,.15)}

/* header */
.hero{position:absolute;left:0;top:0;width:1200px;height:540px;background:linear-gradient(180deg,#9fbfdc 0%,#c9d9e6 38%,#7f8e9c 60%,#5d6670 100%)}
.hero-curve{position:absolute;left:0;top:470px}
.logo{position:absolute;left:40px;top:10px;width:140px;height:140px;border-radius:50%;background:var(--white);border:6px solid var(--blue);display:flex;align-items:center;justify-content:center;text-align:center;font-family:"Bebas Neue",Impact,sans-serif;font-size:26px;line-height:1;color:var(--blue);box-shadow:var(--shadow);z-index:3}
.nav{position:absolute;left:290px;top:54px;width:866px;height:56px;background:var(--blue);border-radius:4px;display:flex;align-items:center;padding-left:26px;gap:38px;z-index:2}
.nav a{font-family:"Bebas Neue",Impact,sans-serif;font-size:20px;color:var(--white);text-decoration:none}
.hero-line{position:absolute;left:0;width:1200px;text-align:center;font-family:"Orbitron",sans-serif;font-size:33px;color:var(--white);letter-spacing:2px;text-shadow:0 2px 6px rgba(0,0,0,.45)}
.hero-arrow{position:absolute;top:280px}

/* social feed */
.feed-card{position:absolute;background:var(--white);box-shadow:var(--shadow)}
.feed-card .avatar{position:absolute;width:36px;height:36px;border-radius:50%;background:linear-gradient(135deg,#c9b8a8,#7d8c9a)}
.feed-card p{position:absolute;font-size:14px;line-height:26px;color:var(--ink)}
.feed-card .net{position:absolute;width:10px;height:10px;border-radius:50%;background:var(--blue)}

/* contact */
.contact-band{position:absolute;left:0;top:1188px;width:1200px;height:286px;background:linear-gradient(90deg,#2a86e6 0%,#4a9cf0 40%,#1f7fe3 100%)}
.contact-info{position:absolute;color:var(--white)}
.contact-info .label{font-family:"Bebas Neue",Impact,sans-serif;font-size:23px}
.contact-info .value{font-size:19px;color:#e7f1fd}
.form-card{position:absolute;left:598px;top:1120px;width:486px;height:424px;background:var(--white);box-shadow:var(--shadow)}
.field{position:absolute;left:44px;width:406px;border-bottom:1px solid var(--line);font-size:14px;color:var(--muted);padding-left:10px;padding-bottom:8px}

/* about */
.about-text{position:absolute;left:644px;top:1700px;width:420px;font-size:19px;line-height:34px;color:var(--ink)}

/* services */
.service{position:absolute;width:366px;height:246px;overflow:hidden}
.service span{position:absolute;left:0;bottom:28px;width:100%;text-align:center;font-family:"Bebas Neue",Impact,sans-serif;font-size:33px;color:var(--white);text-shadow:0 2px 5px rgba(0,0,0,.6)}

/* testimonials */
.testimonial{position:absolute;top:2976px;width:328px;height:296px;background:var(--white);box-shadow:0 3px 10px rgba(0,0,0,.16);overflow:hidden}
.testimonial .quote{position:absolute;left:40px;top:10px;font-family:Georgia,serif;font-size:64px;font-weight:700;color:var(--blue-pale)}
.testimonial .face{position:absolute;left:124px;top:54px;width:76px;height:76px;border-radius:50%;border:4px solid var(--blue-pale);background:linear-gradient(135deg,#d9c3ad,#8b6f5a)}
.testimonial p{position:absolute;left:52px;top:150px;width:236px;font-size:14px;line-height:26px;color:var(--ink)}

/* gallery */
.gallery-label{position:absolute;left:36px;top:3556px;width:406px;text-align:center;font-family:"Bebas Neue",Impact,sans-serif;font-size:32px;color:var(--white);text-shadow:0 2px 6px rgba(0,0,0,.6)}

/* resources */
.resources-text{position:absolute;left:236px;top:3982px;width:736px;font-size:19px;line-height:34px;color:var(--white)}

/* blog */
.post{position:absolute;top:4440px;width:306px;height:292px;box-shadow:var(--shadow);overflow:hidden}
.post .date{position:absolute;left:0;top:0;width:80px;height:60px;background:rgba(26,130,232,.85);display:flex;align-items:center;justify-content:center;font-family:"Bebas Neue",Impact,sans-serif;font-size:24px;color:var(--white)}

/* footer */
.footer{position:absolute;left:0;top:4780px;width:1200px;height:392px;background:var(--blue)}
.foot-head{position:absolute;font-family:"Bebas Neue",Impact,sans-serif;font-size:23px;color:var(--white)}
.foot-text{position:absolute;font-size:19px;color:var(--white);line-height:36px}
.foot-field{position:absolute;left:596px;width:236px;border-bottom:1px solid #9cc7f5;font-size:13px;color:var(--white);padding:0 0 8px 10px}
.foot-link{position:absolute;left:912px;font-size:14px;color:var(--white)}
.copyright{position:absolute;left:0;top:5114px;width:1200px;text-align:center;font-size:14px;color:var(--white)}
</style>
</head>
<body>

<!-- HEADER / HERO -->
<div class="hero" role="img" aria-label="Large modern industrial warehouse building under a blue sky"></div>
<svg class="hero-curve abs" width="1200" height="72" viewBox="0 0 1200 72"><path d="M0 32 Q600 80 1200 4 L1200 72 L0 72Z" fill="#ffffff"/></svg>
<div class="logo">TRI-BAY<br>GROUP</div>
<nav class="nav">
  <a>Home</a><a>About Us</a><a>Services</a><a>Blog</a><a>Testimonials</a><a>Projects</a><a>Resources</a><a>Contact Us</a>
</nav>
<div class="hero-line" style="top:246px">WE OFFER RELIABLE</div>
<div class="hero-line" style="top:302px">WORD-OF-MOUTH</div>
<div class="hero-line" style="top:358px">EVIDENCE OF QUALITY WORKMANSHIP</div>
<svg class="hero-arrow" style="left:80px" width="30" height="24" viewBox="0 0 30 24"><path d="M28 12H4M12 3L3 12l9 9" fill="none" stroke="#111" stroke-width="3"/></svg>
<svg class="hero-arrow" style="left:1086px" width="30" height="24" viewBox="0 0 30 24"><path d="M2 12h24M18 3l9 9-9 9" fill="none" stroke="#111" stroke-width="3"/></svg>

<!-- SOCIAL MEDIA FEED -->
<div class="section-title" style="top:590px">Social Media Feed</div>

<div class="feed-card" style="left:0;top:656px;width:176px;height:140px">
  <div class="avatar" style="left:8px;top:20px"></div>
  <p style="left:56px;top:14px;width:112px">Lorem ipsum dolor sit amet, consectetur</p>
  <div class="abs" style="left:44px;top:96px;color:var(--gold);font-size:17px;letter-spacing:2px">★★★★★</div>
</div>
<div class="photo" style="left:0;top:810px;width:178px;height:190px;background:linear-gradient(135deg,#2f6fa8,#d0764a 55%,#3a4a6a)" role="img" aria-label="Hands holding smartphones"></div>

<div class="feed-card" style="left:192px;top:658px;width:252px;height:284px">
  <div class="photo" style="left:0;top:0;width:252px;height:168px;background:linear-gradient(135deg,#d7e4f2,#8db2dc 50%,#c99a7d)" role="img" aria-label="People sharing posts on phones with social reaction icons"></div>
  <div class="avatar" style="left:24px;top:196px"></div>
  <p style="left:76px;top:188px;width:160px">Lorem ipsum dolor sit amet, consectetur adipiscing elit, sed do</p>
  <div class="net" style="left:232px;top:262px"></div>
</div>

<div class="feed-card" style="left:470px;top:700px;width:252px;height:298px">
  <div class="photo" style="left:0;top:0;width:252px;height:168px;background:linear-gradient(135deg,#1c2340,#c4502e 50%,#f0b23a)" role="img" aria-label="Woman smiling at her phone surrounded by glowing social icons"></div>
  <div class="avatar" style="left:24px;top:194px"></div>
  <p style="left:76px;top:190px;width:160px">Lorem ipsum dolor sit amet, consectetur adipiscing elit, sed do</p>
  <div class="net" style="left:232px;top:276px"></div>
</div>

<div class="feed-card" style="left:752px;top:658px;width:254px;height:284px">
  <div class="photo" style="left:0;top:0;width:254px;height:168px;background:linear-gradient(135deg,#4b5663,#a88a6c 55%,#d9cdbf)" role="img" aria-label="Woman using a smartphone at a desk"></div>
  <div class="avatar" style="left:24px;top:196px"></div>
  <p style="left:76px;top:188px;width:160px">Lorem ipsum dolor sit amet, consectetur adipiscing elit, sed do</p>
  <div class="net" style="left:232px;top:262px"></div>
</div>

<div class="photo" style="left:1062px;top:658px;width:138px;height:156px;background:linear-gradient(135deg,#e3e6ea,#8c939c 60%,#3d4248)" role="img" aria-label="Hand on a laptop with communication icons"></div>
<div class="photo" style="left:1034px;top:850px;width:166px;height:150px;background:linear-gradient(135deg,#3b1f5c,#c24b8a 55%,#2a64b8)" role="img" aria-label="Phone with floating social reaction icons"></div>

<!-- CONTACT -->
<div class="contact-band" role="img" aria-label="Blue-tinted architectural drawings and drafting tools"></div>
<svg class="abs" style="left:202px;top:1248px" width="24" height="24" viewBox="0 0 24 24"><path d="M6.6 10.8a15 15 0 0 0 6.6 6.6l2.2-2.2c.3-.3.7-.4 1-.2 1.1.4 2.3.6 3.6.6.6 0 1 .4 1 1V20c0 .6-.4 1-1 1C10.6 21 3 13.4 3 4c0-.6.4-1 1-1h3.5c.6 0 1 .4 1 1 0 1.3.2 2.5.6 3.6.1.3 0 .7-.2 1z" fill="#fff"/></svg>
<div class="contact-info" style="left:246px;top:1248px"><div class="label">Call Us</div></div>
<div class="contact-info" style="left:246px;top:1290px"><div class="value">+1 888 888 8888</div></div>
<svg class="abs" style="left:202px;top:1340px" width="22" height="28" viewBox="0 0 22 28"><path d="M11 1C5.5 1 1 5.4 1 10.8 1 18 11 27 11 27s10-9 10-16.2C21 5.4 16.5 1 11 1zm0 14a4 4 0 1 1 0-8 4 4 0 0 1 0 8z" fill="#fff"/></svg>
<div class="contact-info" style="left:246px;top:1342px"><div class="label">Location</div></div>
<div class="contact-info" style="left:246px;top:1384px"><div class="value">Lorem Ipsum Sie Amet,</div></div>

<div class="form-card">
  <div class="heading abs" style="left:44px;top:40px;font-size:30px;color:var(--blue)">Contact Us</div>
  <div class="field" style="top:116px">Name</div>
  <div class="field" style="top:184px">Email address</div>
  <div class="field" style="top:252px">Message</div>
  <div class="btn" style="left:44px;top:330px;width:138px;height:46px">Contact Us</div>
</div>

<!-- ABOUT -->
<svg class="abs" style="left:0;top:1524px" width="598" height="638" viewBox="0 0 598 638" role="img" aria-label="Glass office tower seen from below beside green trees">
  <defs><linearGradient id="aboutFill" x1="0" y1="0" x2="1" y2="1"><stop offset="0" stop-color="#aac7e4"/><stop offset=".5" stop-color="#5f86ad"/><stop offset="1" stop-color="#5a8c46"/></linearGradient></defs>
  <path d="M0 0 L598 66 L598 638 L0 638Z" fill="url(#aboutFill)"/>
</svg>
<div class="section-title" style="left:644px;width:400px;top:1636px">About Us</div>
<div class="about-text">Sed ut perspiciatis unde omnis iste natus error sit voluptatem accusantium doloremque laudantium, totam rem aperiam, eaque ipsa quae ab illo inventore veritatis et quasi architecto beatae vitae dicta sunt explicabo. Nemo enim ipsam voluptatem quia voluptas sit aspernatur aut odit aut fugit, sed quia consequuntur magni dolores eos qui ratione voluptatem sequi nesciunt. Neque porro quisquam est, qui dolorem ipsum quia dolor</div>
<div class="btn" style="left:772px;top:2066px;width:140px;height:42px">Read More</div>

<!-- SERVICES -->
<svg class="abs" style="left:0;top:2200px" width="1200" height="640" viewBox="0 0 1200 640"><path d="M0 0H1200V616Q600 580 600 640Q600 580 0 616Z" fill="#1f80e6"/></svg>
<div class="section-title on-blue" style="top:2222px">Services</div>
<div class="service" style="left:28px;top:2288px"><div class="photo" style="inset:0;background:linear-gradient(135deg,#d8c9a8,#7f8b4f 50%,#4b5a64)" role="img" aria-label="Two contractors in hard hats reviewing plans"></div><span>General Contractors</span></div>
<div class="service" style="left:416px;top:2288px"><div class="photo" style="inset:0;background:linear-gradient(135deg,#f2ede6,#b9a48c 60%,#7a6a58)" role="img" aria-label="Renovated bright interior with staircase"></div><span>Home Renovations</span></div>
<div class="service" style="left:806px;top:2288px"><div class="photo" style="inset:0;background:linear-gradient(135deg,#5c5e62,#2d2f33 60%,#8a6f52)" role="img" aria-label="Modern dark commercial building exterior"></div><span>Commercial Construction</span></div>
<div class="service" style="left:210px;top:2564px"><div class="photo" style="inset:0;background:linear-gradient(135deg,#6f8aa0,#3d4b3a 55%,#7f9a4e)" role="img" aria-label="House with landscaped front garden"></div><span>Exterior Spaces</span></div>
<div class="service" style="left:598px;top:2564px"><div class="photo" style="inset:0;background:linear-gradient(135deg,#d9b88c,#9b7550 55%,#5d4632)" role="img" aria-label="Timber-framed home addition under construction"></div><span>Additions</span></div>

<!-- TESTIMONIALS -->
<div class="section-title" style="top:2918px">Testimonials</div>
<svg width="0" height="0" style="position:absolute">
  <defs>
    <g id="bubble">
      <path d="M38 0h218a34 34 0 0 1 34 34v84a34 34 0 0 1-34 34H180l-6 42-26-42H38A34 34 0 0 1 4 118V34A34 34 0 0 1 38 0z" fill="none" stroke="#cfe4fb" stroke-width="3"/>
    </g>
    <g id="corners">
      <path d="M300 0a28 28 0 0 0 28 28" fill="none" stroke="#cfe4fb" stroke-width="7"/>
      <path d="M0 268a28 28 0 0 1 28 28" fill="none" stroke="#cfe4fb" stroke-width="7"/>
    </g>
  </defs>
</svg>
<div class="testimonial" style="left:96px">
  <svg class="abs" style="left:0;top:0" width="328" height="296"><use href="#corners"/><g transform="translate(20 88)"><use href="#bubble"/></g></svg>
  <div class="quote">“</div><div class="face" role="img" aria-label="Client portrait"></div>
  <p>Lorem ipsum dolor sit amet, consectetur adipiscing elit, sed do eiusmod tempor incididunt ut</p>
</div>
<div class="testimonial" style="left:432px">
  <svg class="abs" style="left:0;top:0" width="328" height="296"><use href="#corners"/><g transform="translate(20 88)"><use href="#bubble"/></g></svg>
  <div class="quote">“</div><div class="face" role="img" aria-label="Client portrait"></div>
  <p>Lorem ipsum dolor sit amet, consectetur adipiscing elit, sed do eiusmod tempor incididunt ut</p>
</div>
<div class="testimonial" style="left:770px">
  <svg class="abs" style="left:0;top:0" width="328" height="296"><use href="#corners"/><g transform="translate(20 88)"><use href="#bubble"/></g></svg>
  <div class="quote">“</div><div class="face" role="img" aria-label="Client portrait"></div>
  <p>Lorem ipsum dolor sit amet, consectetur adipiscing elit, sed do eiusmod tempor incididunt ut</p>
</div>

<!-- GALLERY -->
<div class="photo" style="left:36px;top:3324px;width:406px;height:496px;background:linear-gradient(135deg,#5a5651,#2f2d2b 55%,#8d8378)" role="img" aria-label="Dark living room with sofa and artwork"></div>
<div class="abs" style="left:36px;top:3818px;width:406px;height:4px;background:var(--blue)"></div>
<div class="gallery-label">Gallery</div>
<div class="photo" style="left:444px;top:3324px;width:238px;height:246px;background:linear-gradient(180deg,#f0f0ee,#b7a58d)" role="img" aria-label="Bright modern open-plan interior with high ceiling"></div>
<div class="photo" style="left:684px;top:3324px;width:238px;height:246px;background:linear-gradient(180deg,#b9cde2,#e9e8e4 55%,#6f8a4e)" role="img" aria-label="White house with solar panels on the roof"></div>
<div class="photo" style="left:924px;top:3324px;width:238px;height:246px;background:linear-gradient(180deg,#4c6a36,#9a7a58)" role="img" aria-label="Wooden deck surrounded by greenery"></div>
<div class="photo" style="left:444px;top:3574px;width:238px;height:246px;background:linear-gradient(180deg,#e6e8ea,#9a7656)" role="img" aria-label="Kitchen cabinets being installed"></div>
<div class="photo" style="left:684px;top:3574px;width:238px;height:246px;background:linear-gradient(135deg,#9fb3c6,#e2762c 55%,#6a5a4c)" role="img" aria-label="Worker in orange vest at a construction site"></div>
<div class="photo" style="left:924px;top:3574px;width:238px;height:246px;background:linear-gradient(135deg,#6d8a5a,#2f3440 55%,#8b5e44)" role="img" aria-label="Screened porch with outdoor furniture"></div>
<svg class="abs" style="left:10px;top:3566px" width="22" height="16" viewBox="0 0 22 16"><path d="M20 8H3M9 2L3 8l6 6" fill="none" stroke="#1a82e8" stroke-width="2"/></svg>
<svg class="abs" style="left:1170px;top:3566px" width="22" height="16" viewBox="0 0 22 16"><path d="M2 8h17M13 2l6 6-6 6" fill="none" stroke="#1a82e8" stroke-width="2"/></svg>

<!-- RESOURCES -->
<svg class="abs" style="left:0;top:3870px" width="1200" height="440" viewBox="0 0 1200 440"><path d="M0 0Q600 -16 1200 10V410Q600 450 0 420Z" fill="#1f80e6"/></svg>
<div class="section-title on-blue" style="top:3916px">Resources</div>
<div class="resources-text">Sed ut perspiciatis unde omnis iste natus error sit voluptatem accusantium doloremque laudantium, totam rem aperiam, eaque ipsa quae ab illo inventore veritatis et quasi architecto beatae vitae dicta sunt explicabo. Nemo enim ipsam voluptatem quia voluptas sit aspernatur aut odit aut fugit, sed quia consequuntur magni dolores eos qui ratione voluptatem sequi nesciunt. Neque porro quisquam est, qui dolorem ipsum quia dolor sit amet, consectetur, adipisci velit, sed quia</div>
<div class="btn" style="left:518px;top:4230px;width:160px;height:42px;border:none">Download PDF</div>

<!-- BLOG -->
<div class="section-title" style="top:4374px">Blog</div>
<div class="post" style="left:118px"><div class="photo" style="inset:0;background:linear-gradient(135deg,#f2efe9,#b7b2aa 55%,#7c766d)" role="img" aria-label="Laptop keyboard and eyeglasses"></div><div class="date">Jan 6</div></div>
<div class="post" style="left:446px"><div class="photo" style="inset:0;background:linear-gradient(135deg,#9a6f62,#5a4c57 55%,#2b2a33)" role="img" aria-label="Hands typing on a keyboard"></div><div class="date">Jun 23</div></div>
<div class="post" style="left:772px"><div class="photo" style="inset:0;background:linear-gradient(135deg,#3a3432,#8a5a3a 55%,#c08a5a)" role="img" aria-label="Person working at a laptop on a wooden desk"></div><div class="date">Jan 1</div></div>

<!-- FOOTER -->
<div class="footer"></div>
<div class="abs" style="left:110px;top:4840px;width:140px;height:140px;border-radius:50%;background:var(--white);display:flex;align-items:center;justify-content:center;text-align:center;font-family:'Bebas Neue',Impact,sans-serif;font-size:26px;line-height:1;color:var(--blue)">TRI-BAY<br>GROUP</div>

<div class="foot-head" style="left:328px;top:4810px">Get In Touch</div>
<svg class="abs" style="left:330px;top:4872px" width="22" height="22" viewBox="0 0 24 24"><path d="M6.6 10.8a15 15 0 0 0 6.6 6.6l2.2-2.2c.3-.3.7-.4 1-.2 1.1.4 2.3.6 3.6.6.6 0 1 .4 1 1V20c0 .6-.4 1-1 1C10.6 21 3 13.4 3 4c0-.6.4-1 1-1h3.5c.6 0 1 .4 1 1 0 1.3.2 2.5.6 3.6.1.3 0 .7-.2 1z" fill="#fff"/></svg>
<div class="foot-text" style="left:374px;top:4864px">+1 888 888 8888</div>
<svg class="abs" style="left:332px;top:4924px" width="20" height="26" viewBox="0 0 22 28"><path d="M11 1C5.5 1 1 5.4 1 10.8 1 18 11 27 11 27s10-9 10-16.2C21 5.4 16.5 1 11 1zm0 14a4 4 0 1 1 0-8 4 4 0 0 1 0 8z" fill="#fff"/></svg>
<div class="foot-text" style="left:374px;top:4918px;width:180px">Lorem Ipsum Sie Amet,</div>
<svg class="abs" style="left:328px;top:5030px" width="28" height="20" viewBox="0 0 28 20"><rect x="1" y="1" width="26" height="18" fill="none" stroke="#fff" stroke-width="2"/><path d="M1 1l13 10L27 1" fill="none" stroke="#fff" stroke-width="2"/></svg>
<div class="foot-text" style="left:374px;top:5022px">hello@tribaygroup.com</div>

<div class="foot-head" style="left:594px;top:4810px">Send Us A Message</div>
<div class="foot-field" style="top:4876px">Name</div>
<div class="foot-field" style="top:4932px">Email address</div>
<div class="foot-field" style="top:4988px">Message</div>
<div class="btn" style="left:596px;top:5040px;width:106px;height:40px;border:none;box-shadow:none">Submit</div>

<div class="foot-head" style="left:910px;top:4810px">Services</div>
<div class="foot-link" style="top:4872px">General Contractors</div>
<div class="foot-link" style="top:4915px">Home Renovations</div>
<div class="foot-link" style="top:4958px">Additions</div>
<div class="foot-link" style="top:5001px">Exterior Spaces</div>
<div class="foot-link" style="top:5044px">Commercial Construction</div>

<div class="copyright">@COPYRIGHTS 2023. TBG. ALL RIGHTS RESERVED.</div>

</body>
</html>
```